Grey Fennel Medical Website to make connecting and communicating easier

To create a unique, user-friendly, professional website for patients and professionals to access education/ information, forms, appointments, contact details, and data about us, and for us to have the capacity to link to various cloud-based platforms.
To use the logo design and colour scheme we have just sourced.

WEBSITE to be eye catching, Inspiring and alluring
- efficient and logical
- professional and trustworthy appearance
- health focus "living health matters"
- user friendly
- ability to link with cloud-based software and video conferencing tools/ telehealth
- colours- black/ white teal and ?silver

PAGES:
page 1 - Our clinic and staff, services offered, contact us- address/ map / contact details- social media connections
page 2- patients and visitors - New patient forms to complete, news and patient informtion (educatinal)
page 3 - health professionals -referral forms, research and education
page 3- online appointments
page 4 - Quick links - partners, other services
page 5- privacy policy, disclaimer

HI, Could we please extend the deadline another 5 days, so sorry just struggling with my workload to be able to keep up and I am wanting to liaise more with the designer that I will choose. I am so happy with SketchHarbor and all the designers - thank you! Thank you so much!!

Target Market(s)

Patients - mostly over 60's so the website must be minimal clicks and simple to navigate
Professionals - for education and access forms

Industry/Entity Type

Health Care

Coding

Coded - Design and coding required

Number of Pages Required

5+ page

Font styles to use
Sans Serif
Script

Colors
33b8a4
86cfc6

Requirements
Must have
• WEBSITE to be eye catching, Inspiring and alluring
- efficient and logical
- user friendly

WEBSITE - professional and user friendly
- ability to link with cloud based software and videoconferencing/ telehealth
Nice to have
• clean and crisp presentation
happy for an innovative look
room to add more services and ability to link pages and resources
Should not have
• Please ensure the website is not:
clunky
difficult to navigate
common and cheap looking

```html
<!DOCTYPE html>
<html lang="en">
<head>
<meta charset="utf-8">
<title>Grey Fennel Medical</title>
<link href="https://fonts.googleapis.com/css2?family=Poppins:wght@400;500&family=Open+Sans:wght@400&display=swap" rel="stylesheet">
<style>
:root{
  --teal:#33b8a4;
  --teal-dark:#1f9d8a;
  --teal-soft:#86cfc6;
  --ink:#222;
  --text:#3a3a3a;
  --grey-line:#c9c9c9;
  --footer:#242424;
  --footer-text:#bdbdbd;
}
*{box-sizing:border-box;margin:0;padding:0}
html,body{width:1200px;height:2605px;overflow:hidden;background:#fff}
body{position:relative;font-family:"Open Sans",sans-serif;color:var(--text)}
.abs{position:absolute}
.btn{position:absolute;background:var(--teal);color:#fff;font-family:"Poppins",sans-serif;display:flex;align-items:center;justify-content:center;text-decoration:none}

/* header */
.brand{left:144px;top:52px;display:flex;align-items:center;gap:10px;font-family:"Poppins",sans-serif;font-size:19px;font-weight:500;color:var(--teal);line-height:1.1}
.brand-dot{width:18px;height:18px;border-radius:50%;background:var(--teal)}
.appt{left:783px;top:26px;width:273px;height:48px;font-size:18px;gap:10px}
.nav{left:333px;top:108px;width:723px;display:flex;justify-content:space-between;font-family:"Poppins",sans-serif;font-size:15px;color:var(--ink)}
.nav span.active{color:var(--teal)}
.caret{display:inline-block;border:4px solid transparent;border-top:5px solid var(--ink);border-bottom:0;margin-left:4px;vertical-align:middle}

/* hero */
.hero{left:0;top:147px;width:1200px;height:467px;background:linear-gradient(90deg,#b9aea3 0%,#d9d6d3 35%,#e8e8ec 60%,#ecebef 100%)}
.hero-title{right:145px;top:298px;text-align:right;font-family:"Poppins",sans-serif;font-size:33px;line-height:48px;color:var(--ink);font-weight:400}
.hero-btn{left:911px;top:409px;width:145px;height:48px;font-size:19px}
.arrow{width:40px;height:40px;border-radius:50%;background:#fff;top:361px;display:flex;align-items:center;justify-content:center}

/* clinic */
.section-title{font-family:"Poppins",sans-serif;font-size:33px;color:var(--teal);font-weight:400}
.clinic-title{left:144px;top:752px}
.clinic-text{left:145px;top:808px;width:525px;font-size:13.4px;line-height:25.6px}
.clinic-btn{left:144px;top:979px;width:104px;height:40px;font-size:13px}
.staff{width:176px;height:192px;background:linear-gradient(180deg,#8d847d,#c9c3bd 70%,#ecebea)}
.staff-name{position:absolute;bottom:4px;width:100%;text-align:center;font-family:"Poppins",sans-serif;font-size:15px;color:#111}

/* services */
.services{left:0;top:1169px;width:1200px;height:520px;background:linear-gradient(120deg,#3cb9a6 0%,#2aa893 50%,#3bbda9 100%)}
.services-title{left:0;top:1240px;width:1200px;text-align:center;color:#fff;font-family:"Poppins",sans-serif;font-size:32px;font-weight:400}
.card{top:1306px;width:298px;height:296px;background:#fff;text-align:center}
.card svg{position:absolute;left:117px;top:30px}
.card h3{position:absolute;top:112px;width:100%;font-family:"Poppins",sans-serif;font-weight:400;font-size:24px;color:var(--ink)}
.card p{position:absolute;top:152px;left:12px;right:12px;font-size:11.4px;line-height:20.5px;color:#444}
.card .btn{left:97px;top:224px;width:104px;height:40px;font-size:13px}

/* contact */
.contact-title{left:0;top:1760px;width:1200px;text-align:center}
.contact-text{left:145px;top:1818px;width:392px;font-size:11.5px;line-height:24px}
.contact-line{left:145px;display:flex;align-items:center;gap:10px;font-family:"Poppins",sans-serif;font-weight:500;font-size:28px;color:#111}
.contact-icon{width:32px;height:32px;border-radius:50%;background:#dff3ef;display:flex;align-items:center;justify-content:center}
.field{border:1px solid var(--grey-line);font-size:13px;color:#8b8b8b;padding:12px 15px;height:40px}
.submit{left:782px;top:2008px;width:104px;height:45px;border-radius:23px;background:var(--teal-dark);font-size:16px}

/* map */
.map{left:144px;top:2092px;width:912px;height:320px;background:linear-gradient(135deg,#cfcfcf,#bdbdbd 50%,#d3d3d3)}
.map-bar{left:144px;top:2358px;width:912px;height:54px;background:rgba(235,235,235,.85);text-align:center;font-family:"Poppins",sans-serif;font-size:24px;line-height:54px;color:#2a2a2a}

/* footer */
.footer{left:0;top:2493px;width:1200px;height:112px;background:var(--footer)}
.foot-links{left:145px;font-size:10.8px;color:var(--footer-text)}
.foot-links i{font-style:normal;margin:0 9px}
.social{top:2538px;width:22px;height:22px;border-radius:50%;background:#9a9a9a}
</style>
</head>
<body>

<header>
  <div class="abs brand"><span class="brand-dot"></span>Grey Fennel Medical</div>
  <a class="btn appt">
    <svg width="15" height="15" viewBox="0 0 16 16" fill="none" stroke="#fff" stroke-width="1.5"><rect x="1.5" y="3" width="13" height="11.5"/><path d="M1.5 6.5h13M5 1v3M11 1v3"/></svg>
    ONLINE APPOINTMENTS
  </a>
  <nav class="abs nav">
    <span class="active">Our Clinic</span>
    <span>Staffs</span>
    <span>Services</span>
    <span>Paitnets &amp; Visitors<i class="caret"></i></span>
    <span>Health Professionals<i class="caret"></i></span>
    <span>Contact Us</span>
  </nav>
</header>

<section>
  <div class="abs hero" role="img" aria-label="Doctor consulting with a patient at a desk in a bright clinic room"></div>
  <div class="abs arrow" style="left:47px"><svg width="14" height="18" viewBox="0 0 14 18"><path d="M10 2 3 9l7 7" fill="none" stroke="var(--teal)" stroke-width="3"/></svg></div>
  <div class="abs arrow" style="left:1111px"><svg width="14" height="18" viewBox="0 0 14 18"><path d="M4 2l7 7-7 7" fill="none" stroke="var(--teal)" stroke-width="3"/></svg></div>
  <h1 class="abs hero-title">Aenean sed quam non<br>faucibus consequat</h1>
  <a class="btn hero-btn">READ MORE</a>
</section>

<section>
  <h2 class="abs section-title clinic-title">Our clinic and staff</h2>
  <p class="abs clinic-text">Aenean sed quam non sapien faucibus consequat vitae sit amet orci. Praesent quis risus mi. In mollis nulla in pulvinar dictum. Vivamus interdum sagittis felis, ut dapibus ligula feugiat ac. In dictum sapien eu tellus finibus fermentum. Aenean faucibus lacus ut mollis commodo. Donec vestibulum odio sem, ac laoreet massa ullamcorper id. Donec molestie nisi et tellus hendrerit vehicula. Nunc eu ligula sed quam pulvinar maximus in vitae eros.</p>
  <a class="btn clinic-btn">Read More</a>
  <div class="abs staff" style="left:695px;top:694px" role="img" aria-label="Portrait of staff member Owen Hale"><span class="staff-name">Owen Hale</span></div>
  <div class="abs staff" style="left:879px;top:710px" role="img" aria-label="Portrait of staff member Mara"><span class="staff-name">Mara</span></div>
  <div class="abs staff" style="left:695px;top:894px" role="img" aria-label="Portrait of staff member Lena"><span class="staff-name">Lena</span></div>
  <div class="abs staff" style="left:879px;top:910px" role="img" aria-label="Portrait of staff member Theo"><span class="staff-name">Theo</span></div>
</section>

<section>
  <div class="abs services" role="img" aria-label="Teal-tinted background of a doctor's desk with stethoscope"></div>
  <h2 class="abs services-title">Services</h2>

  <div class="abs card" style="left:144px">
    <svg width="64" height="60" viewBox="0 0 64 60" fill="none" stroke="#333" stroke-width="1.6"><rect x="2" y="2" width="52" height="40"/><path d="M2 10h52M7 6h2M12 6h2"/><circle cx="17" cy="24" r="6"/><path d="M7 40c1-7 5-10 10-10s9 3 10 10M32 20h16M32 26h12"/><path d="M48 34l12 4v8c0 6-5 10-12 12-7-2-12-6-12-12v-8z"/><path d="M43 46l4 4 7-8"/></svg>
    <h3>Proin dolor</h3>
    <p>Phasellus nisl est, condimentum vitae faucibus in, sollicitudin vel metus. Nunc sit amet consequat risus. Curabitur ac elit leo.</p>
    <a class="btn">Read More</a>
  </div>
  <div class="abs card" style="left:451px">
    <svg width="64" height="60" viewBox="0 0 64 60" fill="none" stroke="#333" stroke-width="1.6"><path d="M14 38C6 38 2 33 2 27s5-10 11-10c2-9 9-15 18-15 9 0 16 6 17 14 8 0 13 5 13 11s-4 11-11 11"/><path d="M20 30v16M28 30v20M36 30v20M44 30v16"/><circle cx="20" cy="49" r="3"/><circle cx="28" cy="54" r="3"/><circle cx="36" cy="54" r="3"/><circle cx="44" cy="49" r="3"/></svg>
    <h3>Aenean sed</h3>
    <p>Phasellus nisl est, condimentum vitae faucibus in, sollicitudin vel metus. Nunc sit amet consequat risus. Curabitur ac elit leo.</p>
    <a class="btn">Read More</a>
  </div>
  <div class="abs card" style="left:759px">
    <svg width="64" height="60" viewBox="0 0 64 60" fill="none" stroke="#333" stroke-width="1.6"><path d="M16 2h26l10 10v46H16z"/><path d="M42 2v10h10M12 6v56h36"/><path d="M22 16h14M22 22h24M22 28h24M22 34h24M22 40h24M22 46h24"/></svg>
    <h3>Praesent quis</h3>
    <p>Phasellus nisl est, condimentum vitae faucibus in, sollicitudin vel metus. Nunc sit amet consequat risus. Curabitur ac elit leo.</p>
    <a class="btn">Read More</a>
  </div>
</section>

<section>
  <h2 class="abs section-title contact-title">Contact Us</h2>
  <p class="abs contact-text">Pellentesque magna orci, placerat at nisl at, porta ultrices turpis. Fusce in eros non orci posuere viverra ut a lectus. In mattis, lorem sit amet consequat placerat, augue nulla mollis turpis.</p>
  <div class="abs contact-line" style="top:1914px">
    <span class="contact-icon"><svg width="14" height="14" viewBox="0 0 16 16"><path d="M4 1l3 4-2 2c1 2 2 3 4 4l2-2 4 3-2 3C7 15 1 9 1 3z" fill="var(--teal)"/></svg></span>555 014 2290
  </div>
  <div class="abs contact-line" style="top:1978px">
    <span class="contact-icon"><svg width="13" height="10" viewBox="0 0 13 10"><rect width="13" height="10" rx="1" fill="var(--teal)"/><path d="M1 1l5.5 4L12 1" stroke="#fff" fill="none"/></svg></span>info@greyfennel.com
  </div>

  <div class="abs field" style="left:613px;top:1825px;width:218px">Full Name</div>
  <div class="abs field" style="left:839px;top:1825px;width:217px">Email Address</div>
  <div class="abs field" style="left:613px;top:1873px;width:218px">Phone Number</div>
  <div class="abs field" style="left:839px;top:1873px;width:217px">Title</div>
  <div class="abs field" style="left:613px;top:1921px;width:443px;height:80px">Message</div>
  <a class="btn submit">Submit</a>

  <div class="abs map" role="img" aria-label="Street map showing the clinic location by the river"></div>
  <svg class="abs" style="left:568px;top:2212px" width="28" height="40" viewBox="0 0 28 40"><path d="M14 1C6.8 1 1 6.6 1 13.6 1 23 14 39 14 39s13-16 13-25.4C27 6.6 21.2 1 14 1z" fill="var(--teal)"/><circle cx="14" cy="13.5" r="5.5" fill="#fff"/></svg>
  <div class="abs map-bar">24 Building name, Street name, City Zipcode</div>
</section>

<footer>
  <div class="abs footer"></div>
  <div class="abs foot-links" style="top:2513px">Our Clinic<i>|</i>Staffs<i>|</i>Services<i>|</i>Paitnets &amp; Visitors<i>|</i>Health Professionals<i>|</i>Contact Us<i>|</i>Online Appointments</div>
  <div class="abs foot-links" style="top:2540px">Partners<i>|</i>Other Services<i>|</i>Privacy Policy<i>|</i>Disclaimer</div>
  <div class="abs foot-links" style="top:2567px">Copyright © 2020 &nbsp;Grey Fennel Medical. &nbsp; All rights reserved.</div>
  <span class="abs social" style="left:942px"></span>
  <span class="abs social" style="left:986px"></span>
  <span class="abs social" style="left:1033px"></span>
</footer>

</body>
</html>
```